Stylish new business card needed!

Hello everyone! I am in need of a new business card design for an alarm company here in Hurricane WV. I have all fonts, color codes and logos provided for you use! We are a young company and like the style of a clean sleek looking business card. Would like it double sided, one side holding the logo and the other with your design!
Target Market(s)
The people that are looking for the newest tech for home automation and security
Industry/Entity Type
Alarm services; Home automation
Contact Information for Business Card
Name of person; position (Sales; Installer); Phone Number (555.418.7260); Employee cell Number; Website (www.GuardedByVelk.example); Employee Email; Double sided
Look and feel
Each slider illustrates characteristics of the customer's brand and the style your logo design should communicate.

```html
<!DOCTYPE html>
<html lang="en">
<head>
<meta charset="utf-8">
<title>Guarded By Velk – Business Card</title>
<link rel="stylesheet" href="https://fonts.googleapis.com/css2?family=Arimo:wght@400;700&display=swap">
<style>
  :root {
    --stage: #2b2e34;
    --card-dark: #1f1e23;
    --brand-orange: #e8894a;
    --brand-grey: #9b9b9d;
    --pattern-light: #a9a9ab;
    --pattern-mid: #9a9a9c;
    --pattern-dark: #8a8a8c;
    --text-light: #f2f2f2;
  }
  * { box-sizing: border-box; margin: 0; padding: 0; }
  html, body { width: 1200px; height: 780px; overflow: hidden; }
  body {
    background: var(--stage);
    font-family: "Arimo", Arial, sans-serif;
    display: flex;
    align-items: center;
    justify-content: center;
    gap: 40px;
  }
  .card {
    position: relative;
    width: 540px;
    height: 308px;
    overflow: hidden;
    border-radius: 3px;
    box-shadow: 0 10px 28px rgba(0,0,0,.45);
  }

  /* Front */
  .card-front { background: var(--card-dark); }
  .front-curves { position: absolute; inset: 0; width: 100%; height: 100%; }
  .holder {
    position: absolute; left: 30px; top: 38px;
  }
  .holder-name {
    font-size: 22px; font-weight: 700; line-height: 1.1;
    color: var(--brand-orange);
    white-space: nowrap;
  }
  .holder-name .surname { color: var(--brand-grey); }
  .holder-role {
    margin-top: 6px; margin-left: 48px;
    font-size: 14px; color: var(--text-light);
    white-space: nowrap;
  }
  .brand-lockup {
    position: absolute; left: 272px; top: 36px; width: 240px;
    text-align: center;
  }
  .brand-name {
    font-size: 29px; font-weight: 400; letter-spacing: .5px;
    color: var(--brand-grey); line-height: 1;
    white-space: nowrap;
  }
  .brand-tagline {
    margin-top: 9px;
    font-size: 7.5px; font-weight: 700; letter-spacing: .6px;
    text-transform: uppercase; color: var(--brand-orange);
    white-space: nowrap;
  }
  .divider {
    position: absolute; left: 218px; top: 146px;
    width: 1.5px; height: 96px; background: var(--text-light);
  }
  .contact-list {
    position: absolute; left: 240px; top: 150px;
    list-style: none;
  }
  .contact-item {
    display: flex; align-items: center; gap: 9px;
    font-size: 14px; color: var(--text-light);
    height: 22px; white-space: nowrap;
  }
  .contact-icon { width: 13px; height: 13px; flex: none; }

  /* Back */
  .card-back {
    background:
      radial-gradient(ellipse at 80% 15%, var(--pattern-light), transparent 60%),
      linear-gradient(160deg, var(--pattern-mid), var(--pattern-dark));
  }
  .back-mark {
    position: absolute; right: 34px; bottom: 40px;
    font-size: 16px; font-weight: 400; letter-spacing: .4px;
    color: #ffffff; white-space: nowrap;
  }
</style>
</head>
<body>

<section class="card card-front" aria-label="Business card front">
  <svg class="front-curves" viewBox="0 0 540 308" preserveAspectRatio="none" aria-hidden="true">
    <path d="M0 118 C60 228 250 290 430 308 L0 308 Z" fill="var(--brand-orange)"/>
    <path d="M22 112 C84 222 266 282 446 302" fill="none" stroke="var(--brand-grey)" stroke-width="3.5"/>
  </svg>

  <div class="holder">
    <p class="holder-name">Marta <span class="surname">Kovalenko</span></p>
    <p class="holder-role">Sales; Installer</p>
  </div>

  <div class="brand-lockup">
    <p class="brand-name">Guarded By Velk</p>
    <p class="brand-tagline">Automation and security services</p>
  </div>

  <span class="divider" aria-hidden="true"></span>

  <ul class="contact-list">
    <li class="contact-item">
      <svg class="contact-icon" viewBox="0 0 16 16" aria-hidden="true"><path d="M4 1 L6.5 4.5 L5 6.2 C6 8.4 7.6 10 9.8 11 L11.5 9.5 L15 12 L13.4 14.6 C7 14.4 1.6 9 1.4 2.6 Z" fill="var(--brand-orange)"/></svg>
      555.418.7260
    </li>
    <li class="contact-item">
      <svg class="contact-icon" viewBox="0 0 16 16" aria-hidden="true"><rect x="4" y="1" width="8" height="14" rx="1.5" fill="none" stroke="var(--brand-orange)" stroke-width="1.6"/><circle cx="8" cy="12.5" r=".9" fill="var(--brand-orange)"/></svg>
      555.302.9184
    </li>
    <li class="contact-item">
      <svg class="contact-icon" viewBox="0 0 16 16" aria-hidden="true"><circle cx="8" cy="8" r="6.5" fill="none" stroke="var(--brand-orange)" stroke-width="1.5"/><ellipse cx="8" cy="8" rx="2.8" ry="6.5" fill="none" stroke="var(--brand-orange)" stroke-width="1.2"/><path d="M1.5 8 H14.5" stroke="var(--brand-orange)" stroke-width="1.2"/></svg>
      www.GuardedByVelk.example
    </li>
    <li class="contact-item">
      <svg class="contact-icon" viewBox="0 0 16 16" aria-hidden="true"><rect x="1" y="3.5" width="14" height="9.5" rx="1" fill="none" stroke="var(--brand-orange)" stroke-width="1.5"/><path d="M1.5 4 L8 9 L14.5 4" fill="none" stroke="var(--brand-orange)" stroke-width="1.5"/></svg>
      info@GuardedByVelk.example
    </li>
  </ul>
</section>

<section class="card card-back" role="img" aria-label="Card back: grey field covered in a repeating embossed brand wordmark pattern, with the company name in white at lower right">
  <p class="back-mark">Guarded By Velk</p>
</section>

</body>
</html>
```